Business Card for beauty technology startup

Design Glimora Business Card for a Beauty, based on the website identity and colors (https://www.glimora-example.com).
Glimora is a beauty tech startup that gathers helpful product info for beauty lovers and consumers (such as availability on stores, price range and product reviews) for makeup products. The card design must be young, colorful but clean, and very modern.

Target Market(s)

woman, 15-35

Industry/Entity Type

Cosmetics

Contact Information for Business Card

Full Name, address, phone

Font styles to use
Other font styles liked:
• Advent Pro

Colors
e34297
86cfc6
ffffff
5c5c5c
e8e8e8
e667a6
b2b2b2

Requirements
Must have
• One full colored side with a creative design and another with card info
• Use Color palette: #95C5C5 and/or #D38AA5
• Use fonts: Advent Pro
• Use website identity: https://www.glimora-example.com
Nice to have
• If needed extra font: Roboto

```html
<!DOCTYPE html>
<html lang="en">
<head>
<meta charset="utf-8">
<title>Glimora Business Card</title>
<link rel="stylesheet" href="https://fonts.googleapis.com/css2?family=Advent+Pro:wght@200;300&family=Roboto:wght@400&family=Roboto+Condensed:wght@700&display=swap">
<style>
  :root {
    --backdrop: #e8e8e8;
    --card: #f7f7f7;
    --rose: #b5739a;
    --rose-deep: #a9668e;
    --rose-faint: #ece1e8;
    --ink: #4a4a4a;
    --white: #ffffff;
  }
  * { box-sizing: border-box; margin: 0; padding: 0; }
  html, body { width: 1200px; height: 886px; overflow: hidden; }
  body {
    background: var(--backdrop);
    display: flex;
    align-items: center;
    justify-content: center;
    gap: 90px;
  }
  .card {
    position: relative;
    width: 350px;
    height: 600px;
    background: var(--card);
    border-radius: 22px;
    box-shadow: 0 6px 24px rgba(0,0,0,0.12);
    overflow: hidden;
  }
  /* Brand side: full colour */
  .brand-side {
    background: linear-gradient(160deg, var(--rose) 0%, var(--rose-deep) 100%);
    display: flex;
    flex-direction: column;
    align-items: center;
  }
  .brand-mark {
    margin-top: 200px;
    width: 84px;
    height: 84px;
    border: 3px solid var(--white);
    border-radius: 50%;
  }
  .brand-name {
    margin-top: 34px;
    font-family: "Advent Pro", sans-serif;
    font-weight: 200;
    font-size: 44px;
    letter-spacing: 9px;
    padding-left: 9px;
    color: var(--white);
  }
  .brand-url {
    position: absolute;
    bottom: 70px;
    left: 0; right: 0;
    text-align: center;
    font-family: "Advent Pro", sans-serif;
    font-weight: 300;
    font-size: 15px;
    letter-spacing: 5px;
    color: var(--white);
  }
  /* Info side */
  .info-side .wordmark {
    position: absolute;
    top: 54px;
    left: 0; right: 0;
    text-align: center;
    font-family: "Advent Pro", sans-serif;
    font-weight: 200;
    font-size: 60px;
    letter-spacing: 12px;
    padding-left: 12px;
    color: var(--rose);
  }
  .ring {
    position: absolute;
    left: 36px;
    top: 290px;
    width: 290px;
    height: 290px;
    border: 9px solid var(--rose-faint);
    border-radius: 50%;
  }
  .details {
    position: absolute;
    left: 60px;
    right: 50px;
    top: 310px;
    font-family: "Roboto", sans-serif;
    color: var(--ink);
  }
  .person-name {
    font-family: "Roboto Condensed", sans-serif;
    font-weight: 700;
    font-size: 25px;
    color: var(--rose);
  }
  .person-role { font-size: 17px; margin-top: 2px; }
  .address { font-size: 15px; line-height: 1.4; margin-top: 18px; }
  .icon-row { display: flex; gap: 12px; margin-top: 16px; }
  .icon {
    width: 24px; height: 24px;
    border-radius: 50%;
    background: var(--rose);
    display: flex; align-items: center; justify-content: center;
  }
  .divider { height: 2px; background: var(--rose); margin: 14px 0 12px; }
  .contacts { font-size: 15px; line-height: 1.45; }
</style>
</head>
<body>
  <section class="card brand-side">
    <div class="brand-mark"></div>
    <div class="brand-name">GLIMORA</div>
    <div class="brand-url">www.glimora-example.com</div>
  </section>

  <section class="card info-side">
    <div class="wordmark">GLIMORA</div>
    <div class="ring"></div>
    <div class="details">
      <div class="person-name">MAYA LINDQVIST</div>
      <div class="person-role">CEO/FOUNDER</div>
      <div class="address">214 Willow Crest Road<br>Portland, Oregon 97201</div>
      <div class="icon-row">
        <span class="icon"><svg width="12" height="12" viewBox="0 0 24 24"><path fill="#fff" d="M6.6 10.8a15 15 0 0 0 6.6 6.6l2.2-2.2a1 1 0 0 1 1-.25 11.4 11.4 0 0 0 3.6.57 1 1 0 0 1 1 1V20a1 1 0 0 1-1 1A17 17 0 0 1 3 4a1 1 0 0 1 1-1h3.5a1 1 0 0 1 1 1c0 1.25.2 2.45.57 3.57a1 1 0 0 1-.25 1z"/></svg></span>
        <span class="icon"><svg width="12" height="12" viewBox="0 0 24 24"><path fill="none" stroke="#fff" stroke-width="2.4" d="M3 6h18v12H3z M3 6l9 7 9-7"/></svg></span>
        <span class="icon"><svg width="12" height="12" viewBox="0 0 24 24"><g fill="none" stroke="#fff" stroke-width="2.2"><circle cx="12" cy="12" r="9"/><path d="M3 12h18M12 3c3 3.5 3 14.5 0 18M12 3c-3 3.5-3 14.5 0 18"/></g></svg></span>
      </div>
      <div class="divider"></div>
      <div class="contacts">555 014 2290<br>info@glimora-example.com<br>www.glimora-example.com</div>
    </div>
  </section>
</body>
</html>
```